New Business Card Design Project

I need a design for business cards, i am an electrical business called "Corvane Electrical and Communications" i need the cards to be double sided with the company logo on the back (attached) the front needs to say my company name, web site, email address, telephone number, and ABN number and electrical license number. I am open to different arrangements of the information but would like the background to be incorporating something electrical or something that looks smart. open to all additional ideas also.

The company colours are orange and grey see logo attached.

Business Name: Corvane Electrical and Communications
Website: corvaneelectricalandcomms.example.com.au
Email: brent@corvaneelectricalandcomms.example.com.au
Telephone(mobile): 0481209736
ABN: 71208349162
Lic No: 418273D

Target Market(s)

Business entities, Project Managers, Accounts, Clients

Industry/Entity Type

Electrician

Contact Information for Business Card

I need a design for business cards, i am an electrical business called "Corvane Electrical and Communications" i need the cards to be double sided with the company logo on the back (attached) the front needs to say my company name

Font styles to use
Serif
Sans Serif

Colors
f37122
5c5c5c

Requirements
Must have
• Must have the Logo on the back open to different ways of it being on the back but had in mind to keep it central but again open to other options
Nice to have
• A real modern cool background that is eye catching yet contemporary
Should not have
• No backgrounds of a light bulb or plug or anything like that

```html
<!DOCTYPE html>
<html lang="en">
<head>
<meta charset="utf-8">
<title>Corvane Electrical and Communications – Business Cards</title>
<link rel="stylesheet" href="https://fonts.googleapis.com/css2?family=Open+Sans:wght@400;600&display=swap">
<style>
  :root {
    --backdrop: #3a3633;
    --card: #141414;
    --card-edge: #1e1e1e;
    --orange: #f39a1e;
    --text: #e6e6e6;
    --silver: #c9c9c9;
    --divider: #5c5c5c;
  }
  * { margin: 0; padding: 0; box-sizing: border-box; }
  html, body {
    width: 1200px; height: 814px; overflow: hidden;
    background: var(--backdrop);
    font-family: "Open Sans", Arial, sans-serif;
  }
  .canvas {
    position: relative; width: 1200px; height: 814px;
  }
  .card {
    position: absolute; top: 252px;
    width: 540px; height: 310px;
    background: var(--card);
    border: 1px solid var(--card-edge);
    box-shadow: 0 10px 28px rgba(0,0,0,.45);
  }
  .card--front { left: 40px; }
  .card--back { left: 620px; }

  /* front */
  .brand {
    position: absolute; left: 32px; top: 128px; width: 175px;
    display: flex; align-items: center; gap: 10px;
  }
  .brand__dot {
    flex: none; width: 14px; height: 14px; border-radius: 50%;
    background: var(--orange);
  }
  .brand__name {
    color: var(--text); font-weight: 600; font-size: 15px; line-height: 1.25;
  }
  .divider {
    position: absolute; left: 222px; top: 88px; width: 1px; height: 150px;
    background: var(--divider);
  }
  .details {
    position: absolute; left: 238px; top: 82px; right: 10px;
    color: var(--text); font-size: 11px; line-height: 19px;
  }
  .details__name {
    color: var(--orange); font-weight: 600; font-size: 15px; line-height: 21px;
  }
  .details__row { display: flex; align-items: center; gap: 7px; white-space: nowrap; }
  .details__row svg { flex: none; width: 11px; height: 11px; }

  /* back */
  .back-brand {
    position: absolute; left: 0; right: 0; top: 112px;
    display: flex; justify-content: center; align-items: center; gap: 14px;
  }
  .back-brand__dot {
    width: 20px; height: 20px; border-radius: 50%; background: var(--silver);
  }
  .back-brand__name {
    color: var(--silver); font-weight: 600; font-size: 24px; line-height: 1.2;
    text-align: left;
  }
  .back-website {
    position: absolute; left: 0; right: 0; top: 210px;
    text-align: center; color: var(--silver);
    font-size: 11px; letter-spacing: 1.2px;
  }
</style>
</head>
<body>
<main class="canvas">
  <section class="card card--front" aria-label="Business card front">
    <div class="brand">
      <span class="brand__dot"></span>
      <span class="brand__name">Corvane Electrical &amp; Communications</span>
    </div>
    <div class="divider"></div>
    <div class="details">
      <p class="details__name">Brent Halden</p>
      <p>CEO/Founder</p>
      <p>ABN: 71208349162</p>
      <p>Lic No: 418273D</p>
      <p class="details__row">
        <svg viewBox="0 0 12 12" aria-hidden="true"><rect x="3" y="0.5" width="6" height="11" rx="1" fill="var(--orange)"/><rect x="4" y="2" width="4" height="7" fill="var(--card)"/></svg>
        0481209736
      </p>
      <p class="details__row">
        <svg viewBox="0 0 12 12" aria-hidden="true"><rect x="0.5" y="2.5" width="11" height="7.5" fill="var(--orange)"/><path d="M0.5 2.5 6 7 11.5 2.5" fill="none" stroke="var(--card)" stroke-width="1"/></svg>
        brent@corvaneelectricalandcomms.example.com.au
      </p>
      <p class="details__row">
        <svg viewBox="0 0 12 12" aria-hidden="true"><circle cx="6" cy="6" r="5.5" fill="var(--orange)"/><path d="M0.5 6h11M6 .5c-2.5 3-2.5 8 0 11M6 .5c2.5 3 2.5 8 0 11" fill="none" stroke="var(--card)" stroke-width=".8"/></svg>
        corvaneelectricalandcomms.example.com.au
      </p>
    </div>
  </section>

  <section class="card card--back" aria-label="Business card back">
    <div class="back-brand">
      <span class="back-brand__dot"></span>
      <span class="back-brand__name">Corvane Electrical<br>&amp; Communications</span>
    </div>
    <p class="back-website">www.corvaneelectricalandcomms.example.com.au</p>
  </section>
</main>
</body>
</html>
```